Stationery and Business Card Design

We need stationary design for our new company lanternfold. Lanternfold is a company that provides city apartment rentals for tourists in Athens We need business cards, letterheads for A4 and A5 and envelopes for A4 A5. The design needs to be modern, friendly and corporate.

Target Market(s)

City Tourists

Industry/Entity Type

Tourism

```html
<!DOCTYPE html>
<html lang="en">
<head>
<meta charset="utf-8">
<title>Lanternfold Stationery</title>
<link rel="stylesheet" href="https://fonts.googleapis.com/css2?family=Raleway:wght@300;400;600&display=swap">
<style>
  :root {
    --plum: #8a1650;
    --plum-deep: #7a1346;
    --charcoal: #3b3a3b;
    --paper: #f4f4f4;
    --paper-edge: #dcdcdc;
    --stage: #e9e9e9;
    --ink: #5a5a5a;
    --white: #ffffff;
  }
  * { box-sizing: border-box; margin: 0; padding: 0; }
  html, body { width: 1200px; height: 874px; overflow: hidden; }
  body {
    background: var(--stage);
    font-family: "Raleway", Arial, sans-serif;
    color: var(--ink);
    position: relative;
  }
  .sheet {
    position: absolute;
    background: var(--paper);
    box-shadow: 0 2px 6px rgba(0,0,0,0.12);
    overflow: hidden;
  }

  /* brand lockup */
  .brand { display: flex; align-items: center; gap: 7px; }
  .brand-square { width: 16px; height: 16px; background: var(--plum); flex: none; }
  .brand-name { font-weight: 400; font-size: 20px; color: var(--plum); letter-spacing: 0.2px; }
  .brand.on-plum .brand-square { background: var(--white); }
  .brand.on-plum .brand-name { color: var(--white); }
  .brand.small .brand-square { width: 11px; height: 11px; }
  .brand.small .brand-name { font-size: 13px; }
  .brand.large .brand-square { width: 22px; height: 22px; }
  .brand.large .brand-name { font-size: 27px; }

  /* A4 letterhead */
  .letterhead-a4 { left: 40px; top: 50px; width: 300px; height: 424px; }
  .letterhead-a4 .brand { position: absolute; top: 38px; left: 0; right: 0; justify-content: center; }
  .letterhead-a4 .footer-band {
    position: absolute; left: 0; right: 0; bottom: 0; height: 26px;
    background: var(--plum); display: flex; align-items: center; justify-content: space-between;
    padding: 0 12px; color: var(--white); font-size: 6.5px; font-weight: 400;
  }
  .letterhead-a4 .footer-band::after {
    content: ""; position: absolute; left: 0; right: 0; bottom: 0; height: 5px; background: var(--charcoal);
  }
  .contact-row { display: flex; gap: 10px; align-items: center; }
  .contact-item { display: flex; align-items: center; gap: 3px; }
  .contact-item svg { width: 7px; height: 7px; fill: var(--white); }

  /* A4 folder cover */
  .cover-a4 { left: 370px; top: 50px; width: 300px; height: 424px; }
  .cover-a4 .brand { position: absolute; top: 44px; left: 0; right: 0; justify-content: center; }
  .cover-a4 .plum-field { position: absolute; left: 0; right: 0; top: 130px; height: 214px; background: var(--plum); }
  .cover-a4 .charcoal-band {
    position: absolute; left: 0; right: 0; bottom: 0; height: 80px; background: var(--charcoal);
    display: flex; align-items: center; justify-content: flex-end; padding-right: 22px;
    color: #d8d8d8; font-size: 8px; letter-spacing: 0.4px;
  }

  /* DL envelope */
  .envelope { left: 700px; top: 50px; width: 460px; height: 220px; }
  .envelope .flap-band {
    position: absolute; left: 0; right: 0; top: 0; height: 62px; background: var(--plum);
    border-radius: 0 0 14px 14px; display: flex; align-items: center; justify-content: center;
  }
  .envelope .flap-band .mark { width: 18px; height: 18px; background: var(--white); }
  .envelope .web { position: absolute; bottom: 60px; left: 0; right: 0; text-align: center; font-size: 7px; color: #777; }

  /* A5 letterhead */
  .letterhead-a5 { left: 700px; top: 300px; width: 460px; height: 230px; }
  .letterhead-a5 .brand { position: absolute; top: 92px; left: 54px; }
  .letterhead-a5 .footer-band {
    position: absolute; left: 0; right: 0; bottom: 0; height: 24px; background: var(--plum);
    color: var(--white); font-size: 6.5px; display: flex; align-items: center; padding-left: 14px;
  }
  .letterhead-a5 .footer-band::after {
    content: ""; position: absolute; left: 0; right: 0; bottom: 0; height: 5px; background: var(--charcoal);
  }

  /* business cards */
  .card { width: 250px; height: 140px; }
  .card-front { left: 40px; top: 510px; background: var(--plum); }
  .card-front .brand { position: absolute; inset: 0; justify-content: center; }
  .card-front::after { content: ""; position: absolute; left: 0; right: 0; bottom: 0; height: 7px; background: var(--charcoal); }

  .card-back { left: 40px; top: 670px; background: var(--paper); }
  .card-back .brand { position: absolute; top: 16px; right: 16px; }
  .card-back .person { position: absolute; left: 16px; top: 54px; }
  .person-name { font-size: 8px; font-weight: 600; color: var(--plum); letter-spacing: 0.6px; }
  .person-role { font-size: 6.5px; color: var(--ink); margin-top: 2px; }
  .card-back .details {
    position: absolute; left: 0; right: 0; bottom: 0; height: 42px; background: var(--plum);
    color: var(--white); font-size: 6.5px; line-height: 1.5; padding: 7px 16px;
    display: flex; justify-content: space-between;
  }
  .card-back .details::after { content: ""; position: absolute; left: 0; right: 0; bottom: 0; height: 5px; background: var(--charcoal); }

  /* notebook */
  .notebook { left: 370px; top: 510px; width: 240px; height: 320px; }
  .notebook .brand { position: absolute; top: 40px; left: 0; right: 0; justify-content: center; }
  .notebook .plum-field { position: absolute; left: 0; right: 0; top: 110px; height: 150px; background: var(--plum); }
  .notebook .charcoal-band {
    position: absolute; left: 0; right: 0; bottom: 0; height: 60px; background: var(--charcoal);
    color: #d8d8d8; font-size: 7px; display: flex; align-items: center; justify-content: flex-end; padding-right: 16px;
  }
  .notebook .binding { position: absolute; left: 6px; top: 10px; bottom: 10px; width: 8px; }

  /* small goods */
  .key-tag {
    left: 650px; top: 560px; width: 120px; height: 66px; background: var(--white);
    border: 1px solid #cfcfcf; border-radius: 6px; display: flex; align-items: center; justify-content: center;
  }
  .eraser-sleeve {
    left: 650px; top: 660px; width: 120px; height: 44px; background: var(--plum);
    display: flex; align-items: center; justify-content: center;
  }
</style>
</head>
<body>

  <section class="sheet letterhead-a4" aria-label="A4 letterhead">
    <div class="brand"><span class="brand-square"></span><span class="brand-name">Lanternfold</span></div>
    <footer class="footer-band">
      <span>1420 Lantern Row, Athens 105 58</span>
      <span class="contact-row">
        <span class="contact-item"><svg viewBox="0 0 10 10"><path d="M2 1 L4 1 L5 3 L4 4 Q5 6 6 6 L7 5 L9 6 L9 8 Q5 9 1 3 Z"/></svg>+30 210 555 0142</span>
        <span class="contact-item">www.lanternfold.com</span>
      </span>
    </footer>
  </section>

  <section class="sheet cover-a4" aria-label="A4 folder cover">
    <div class="brand large"><span class="brand-square"></span><span class="brand-name">Lanternfold</span></div>
    <div class="plum-field"></div>
    <div class="charcoal-band">www.lanternfold.com</div>
  </section>

  <section class="sheet envelope" aria-label="Envelope">
    <div class="flap-band"><span class="mark"></span></div>
    <p class="web">www.lanternfold.com</p>
  </section>

  <section class="sheet letterhead-a5" aria-label="A5 letterhead">
    <div class="brand"><span class="brand-square"></span><span class="brand-name">Lanternfold</span></div>
    <footer class="footer-band">1420 Lantern Row, Athens 105 58</footer>
  </section>

  <section class="sheet card card-front" aria-label="Business card front">
    <div class="brand on-plum"><span class="brand-square"></span><span class="brand-name">Lanternfold</span></div>
  </section>

  <section class="sheet card card-back" aria-label="Business card back">
    <div class="brand small"><span class="brand-square"></span><span class="brand-name">Lanternfold</span></div>
    <div class="person">
      <p class="person-name">MARA LINDQVIST</p>
      <p class="person-role">Managing Director</p>
    </div>
    <div class="details">
      <span>+30 210 555 0142<br>mara@lanternfold.com</span>
      <span>1420 Lantern Row<br>Athens 105 58</span>
    </div>
  </section>

  <section class="sheet notebook" aria-label="Notebook">
    <svg class="binding" viewBox="0 0 8 300" preserveAspectRatio="none" aria-hidden="true">
      <g fill="none" stroke="#555" stroke-width="1.4">
        <circle cx="4" cy="10" r="2.5"/><circle cx="4" cy="30" r="2.5"/><circle cx="4" cy="50" r="2.5"/>
        <circle cx="4" cy="70" r="2.5"/><circle cx="4" cy="90" r="2.5"/><circle cx="4" cy="110" r="2.5"/>
        <circle cx="4" cy="130" r="2.5"/><circle cx="4" cy="150" r="2.5"/><circle cx="4" cy="170" r="2.5"/>
        <circle cx="4" cy="190" r="2.5"/><circle cx="4" cy="210" r="2.5"/><circle cx="4" cy="230" r="2.5"/>
        <circle cx="4" cy="250" r="2.5"/><circle cx="4" cy="270" r="2.5"/><circle cx="4" cy="290" r="2.5"/>
      </g>
    </svg>
    <div class="brand"><span class="brand-square"></span><span class="brand-name">Lanternfold</span></div>
    <div class="plum-field"></div>
    <div class="charcoal-band">www.lanternfold.com</div>
  </section>

  <section class="sheet key-tag" aria-label="Key tag">
    <div class="brand small"><span class="brand-square"></span><span class="brand-name">Lanternfold</span></div>
  </section>

  <section class="sheet eraser-sleeve" aria-label="Eraser sleeve">
    <div class="brand small on-plum"><span class="brand-square"></span><span class="brand-name">Lanternfold</span></div>
  </section>

</body>
</html>
```